Brookvale Building Company - advertisement poster

I am looking to print some canvas signs to advertise my general contracting company, Brookvale Building Company. The sign will measure 6' long x 3' high so the size should match that ratio. I already have a logo icon, which is the Letter 'B' and some trees that I would like to incorporate, see attached. I would also like the to have the following information listed:
1) phone number: 831-555-0172
2) email: brookvalebuildingcompany@mailnest.example
3) website: brookvalebuildingcompany.example
4) Lic#4826130
5) I want to use this text: "BUILD WITH THE B-CREW!"

The ad should be relatively simple and clean. Black and Green are my company colors. I am open to creative ideas!

Target Market(s)

People looking to renovate their homes

Industry/Entity Type

Construction

Colors
59FF00
82FF00
B8FF75
E3FFCB
F4FFEA

Requirements
Must have
• Must have my company logo
Should not have
• No photos or complex graphics

```html
<!DOCTYPE html>
<html lang="en">
<head>
<meta charset="UTF-8">
<title>Brookvale Building Company – Sign</title>
<link href="https://fonts.googleapis.com/css2?family=Montserrat:wght@400;500;700;800;900&display=swap" rel="stylesheet">
<style>
  :root {
    --page-bg: #e6e8ea;
    --board-bg: #1f1f1f;
    --brand-green: #6cbd45;
    --text-white: #ffffff;
    --text-dark: #1c1c1c;
  }
  * { margin: 0; padding: 0; box-sizing: border-box; }
  html, body {
    width: 1200px;
    height: 800px;
    overflow: hidden;
    background: var(--page-bg);
  }
  .canvas {
    position: relative;
    width: 1200px;
    height: 800px;
    display: flex;
    align-items: center;
    justify-content: center;
  }
  .sign {
    position: relative;
    width: 1120px;
    height: 560px;
    background: var(--board-bg);
    font-family: 'Montserrat', sans-serif;
    color: var(--text-white);
  }
  .brand {
    position: absolute;
    left: 70px;
    top: 70px;
    display: flex;
    align-items: center;
    gap: 16px;
  }
  .brand-mark {
    width: 64px;
    height: 64px;
    background: var(--brand-green);
  }
  .brand-name {
    font-weight: 800;
    font-size: 26px;
    line-height: 1.1;
    text-transform: uppercase;
    letter-spacing: 1px;
    color: var(--text-white);
    width: 260px;
  }
  .licence {
    position: absolute;
    right: 72px;
    top: 172px;
    font-size: 11px;
    font-weight: 500;
  }
  .headline {
    position: absolute;
    left: 0;
    right: 0;
    top: 250px;
    text-align: center;
    font-weight: 900;
    font-size: 70px;
    letter-spacing: 0.5px;
    padding-left: 80px;
  }
  .contact-row {
    position: absolute;
    top: 366px;
    left: 175px;
    right: 100px;
    display: flex;
    align-items: center;
    justify-content: space-between;
  }
  .email {
    display: flex;
    align-items: center;
    gap: 14px;
    font-size: 18px;
    font-weight: 500;
    letter-spacing: 0.3px;
  }
  .phone {
    display: flex;
    align-items: center;
    gap: 10px;
    background: var(--brand-green);
    color: var(--text-dark);
    padding: 6px 14px;
    font-weight: 800;
    font-size: 38px;
    line-height: 1.1;
  }
  .website {
    position: absolute;
    top: 460px;
    left: 0;
    right: 0;
    padding-left: 60px;
    display: flex;
    align-items: center;
    justify-content: center;
    gap: 20px;
    font-size: 40px;
    font-weight: 500;
    letter-spacing: 0.5px;
  }
  .icon { display: block; flex: none; }
</style>
</head>
<body>
<main class="canvas">
  <section class="sign">
    <div class="brand">
      <div class="brand-mark"></div>
      <div class="brand-name">Brookvale Building Company</div>
    </div>

    <p class="licence">Licence No. 4826130</p>

    <h1 class="headline">Build with the B-Crew!</h1>

    <div class="contact-row">
      <p class="email">
        <svg class="icon" width="22" height="15" viewBox="0 0 22 15" aria-hidden="true">
          <rect x="0" y="0" width="22" height="15" fill="var(--brand-green)"/>
          <path d="M0 0 L11 8 L22 0" fill="none" stroke="var(--board-bg)" stroke-width="2"/>
          <path d="M0 15 L8 7 M22 15 L14 7" stroke="var(--board-bg)" stroke-width="1.5"/>
        </svg>
        BrookvaleBuildingCompany@mailnest.example
      </p>
      <p class="phone">
        <svg class="icon" width="24" height="24" viewBox="0 0 24 24" aria-hidden="true">
          <path d="M6.6 10.8a15 15 0 0 0 6.6 6.6l2.2-2.2a1 1 0 0 1 1-.25 11.4 11.4 0 0 0 3.6.57 1 1 0 0 1 1 1V20a1 1 0 0 1-1 1A17 17 0 0 1 3 4a1 1 0 0 1 1-1h3.5a1 1 0 0 1 1 1c0 1.25.2 2.45.57 3.57a1 1 0 0 1-.25 1z" fill="var(--text-dark)"/>
        </svg>
        831.555.0172
      </p>
    </div>

    <p class="website">
      <svg class="icon" width="40" height="40" viewBox="0 0 40 40" aria-hidden="true">
        <g fill="none" stroke="var(--brand-green)" stroke-width="3">
          <circle cx="20" cy="20" r="17"/>
          <ellipse cx="20" cy="20" rx="7.5" ry="17"/>
          <line x1="3" y1="20" x2="37" y2="20"/>
          <line x1="6" y1="11" x2="34" y2="11"/>
          <line x1="6" y1="29" x2="34" y2="29"/>
        </g>
      </svg>
      BrookvaleBuildingCompany.example
    </p>
  </section>
</main>
</body>
</html>
```